Chorus Of Meadowbrook - A Decade of Entertainment

Hello,

My group is called the "Chorus of Meadowbrook" (chorusofmeadowbrook.org), we are a barbershop harmony chorus based in Sacramento. CA and we are celebrating our 10 year anniversary.

We are looking for a full size 8 1/2 x 11 flyer and a standard single sided post card flyer to help market our show.

Target Market(s)

Open Demographic - Family friendly program, Acapella music, 501c3 non-profit corporation, Live Concert

Font styles to use
Serif

Requirements
Must have
• Venue and Date Information:
• Tilden Hall for the Arts, 47 Orchard Bend, Folsom, CA 95812
• Saturday, May 18, 2019
• SHOW TIMES : 2:00pm - 7:00pm
• Special Guests: Silver Quorum - 2006 Grand Tonewell Quartet Laureates
• Tickets: www.chorusofmeadowbrook.org
Nice to have
• We are hoping to have this flyer show our journey over the years to today. I have included photos of past shows over the years, our logo, and a photo of our featured guest performer. We are completely open to your artistic inter and look forward to your offerings. Feel free to contact me with any questions.
• i hae also included three past sgow flyers for your review.

```html
<!DOCTYPE html>
<html lang="en">
<head>
<meta charset="utf-8">
<title>Chorus Of Meadowbrook – Spring Show Flyer</title>
<link href="https://fonts.googleapis.com/css2?family=Roboto+Condensed:wght@500;700&family=Kaushan+Script&family=Lato:wght@700&family=Cormorant+Garamond:ital,wght@1,500&display=swap" rel="stylesheet">
<style>
  :root {
    --page: #e2e2e2;
    --ink: #0b0b0b;
    --night: #070907;
    --gold: #e2b935;
    --gold-deep: #9c7617;
    --gold-mid: #c99d2a;
    --gold-light: #f1d062;
    --text-dark: #111;
  }
  html, body {
    margin: 0; padding: 0;
    width: 1200px; height: 1200px;
    overflow: hidden;
    background: var(--page);
  }
  .flyer {
    position: absolute;
    left: 164px; top: 40px;
    width: 871px; height: 1120px;
    overflow: hidden;
    background: var(--night);
    font-family: "Roboto Condensed", sans-serif;
    color: var(--text-dark);
  }
  .flyer-art { position: absolute; inset: 0; }
  .brand {
    position: absolute; right: 123px; top: 58px;
    text-align: right;
  }
  .brand-name {
    font-family: "Roboto Condensed", sans-serif;
    font-weight: 700; font-size: 34px;
    color: var(--gold); margin: 0; line-height: 1;
  }
  .brand-presents {
    font-family: "Cormorant Garamond", serif;
    font-style: italic; font-weight: 500;
    font-size: 26px; color: var(--gold);
    margin: 8px 62px 0 0; line-height: 1;
  }
  .show-title {
    position: absolute; left: 420px; top: 170px;
    margin: 0; font-family: "Kaushan Script", cursive;
    font-weight: 400; color: var(--gold);
    font-size: 120px; line-height: 1;
  }
  .show-title span { display: block; }
  .show-title .second { margin: -10px 0 0 115px; }
  .caption {
    position: absolute; left: 61px; width: 300px; top: 597px;
    text-align: center; font-weight: 700; font-size: 27px;
    color: var(--gold-light); margin: 0;
  }
  .guests {
    position: absolute; left: 161px; top: 776px;
    width: 548px; height: 60px; box-sizing: border-box;
    border: 1.5px solid var(--text-dark);
    text-align: center;
  }
  .guests-label { font-size: 14px; font-weight: 700; margin: 6px 0 0; line-height: 1; }
  .guests-label em { margin-right: 6px; }
  .guests-title { font-size: 23px; font-weight: 500; margin: 4px 0 0; line-height: 1.1; }
  .date {
    position: absolute; left: 0; right: 0; top: 842px;
    text-align: center; font-weight: 700; font-size: 28px; margin: 0;
  }
  .venue {
    position: absolute; left: 170px; top: 887px;
    width: 527px; height: 76px; box-sizing: border-box;
    border: 1.5px solid var(--text-dark);
    text-align: center; font-size: 23px; font-weight: 500;
    line-height: 29px; padding-top: 8px; margin: 0; font-style: normal;
  }
  .tickets-frame {
    position: absolute; left: 176px; top: 988px;
    width: 519px; height: 54px; box-sizing: border-box;
    border: 1.5px solid var(--text-dark); border-top: none;
    border-radius: 0 0 22px 22px;
  }
  .tickets-frame::before, .tickets-frame::after {
    content: ""; position: absolute; top: 0; width: 120px; height: 22px;
    border-top: 1.5px solid var(--text-dark);
  }
  .tickets-frame::before { left: -1px; border-left: 1.5px solid var(--text-dark); border-radius: 22px 0 0 0; }
  .tickets-frame::after { right: -1px; border-right: 1.5px solid var(--text-dark); border-radius: 0 22px 0 0; }
  .tickets-label {
    position: absolute; left: 0; right: 0; top: 971px;
    text-align: center; font-weight: 500; font-size: 26px; margin: 0;
  }
  .tickets-url {
    position: absolute; left: 212px; top: 1017px;
    width: 445px; height: 51px; border-radius: 26px;
    background: var(--ink); color: var(--gold-light);
    font-family: "Lato", sans-serif; font-weight: 700; font-size: 27px;
    line-height: 51px; text-align: center; margin: 0;
  }
</style>
</head>
<body>
  <article class="flyer">
    <svg class="flyer-art" width="871" height="1120" viewBox="0 0 871 1120" aria-hidden="false">
      <defs>
        <linearGradient id="stageGlow" x1="0" y1="0" x2="0" y2="1">
          <stop offset="0" stop-color="#060806"/>
          <stop offset="0.45" stop-color="#121a26"/>
          <stop offset="1" stop-color="#0a0d10"/>
        </linearGradient>
        <radialGradient id="goldField" cx="0.45" cy="0.55" r="0.75">
          <stop offset="0" stop-color="#f0cd5c"/>
          <stop offset="0.55" stop-color="#c99d2a"/>
          <stop offset="1" stop-color="#8f6c14"/>
        </radialGradient>
        <linearGradient id="arcGold" x1="0" y1="0" x2="1" y2="1">
          <stop offset="0" stop-color="#f6d34a"/>
          <stop offset="1" stop-color="#d8a826"/>
        </linearGradient>
      </defs>

      <rect class="backdrop-photo" x="0" y="160" width="871" height="560" fill="url(#stageGlow)" role="img" aria-label="Photo of the chorus in blue shirts and red ties performing on stage"/>

      <path class="gold-field" d="M0,460 C120,520 250,600 380,700 C480,760 560,790 660,760 C740,735 810,690 871,650 L871,1120 L0,1120 Z" fill="url(#goldField)"/>

      <g class="gold-arcs" fill="none" stroke="url(#arcGold)" stroke-linecap="round">
        <path d="M0,770 C140,790 230,730 240,650" stroke-width="26" opacity="0.9"/>
        <path d="M340,600 C330,700 420,800 560,810" stroke-width="18" opacity="0.8"/>
        <path d="M570,760 C560,860 660,930 780,930 C820,930 850,925 871,918" stroke-width="22" opacity="0.85"/>
      </g>

      <g class="photo-circles">
        <circle cx="211" cy="484" r="177" fill="#1a1410" stroke="var(--gold)" stroke-width="5" role="img" aria-label="Photo of the full chorus on stage in black suits"/>
        <circle cx="479" cy="580" r="111" fill="#8a8a8a" stroke="var(--gold)" stroke-width="5" role="img" aria-label="Black and white photo of guest quartet members"/>
        <circle cx="695" cy="660" r="104" fill="#9a9a9a" stroke="var(--gold)" stroke-width="5" role="img" aria-label="Black and white photo of guest quartet members outdoors"/>
      </g>
    </svg>

    <header class="brand">
      <p class="brand-name">Chorus Of Meadowbrook</p>
      <p class="brand-presents">Presents</p>
    </header>

    <h1 class="show-title"><span>Spring</span><span class="second">Show</span></h1>

    <p class="caption">Meadow Rise</p>

    <section class="guests">
      <p class="guests-label"><em>Special Guests</em>Silver Quorum</p>
      <p class="guests-title">2006 Grand Tonewell Quartet Laureates</p>
    </section>

    <p class="date">Saturday, May 18, 2019 | 2:00pm - 7:00pm</p>

    <address class="venue">Tilden Hall for the Arts, 47 Orchard Bend,<br>Folsom, CA 95812</address>

    <div class="tickets-frame"></div>
    <p class="tickets-label">Tickets available on</p>
    <p class="tickets-url">www.chorusofmeadowbrook.org</p>
  </article>
</body>
</html>
```